Mira Bloom Fitness Coaching Project

I am a personal trainer based in London. My services include one-on-one PT sessions, bootcamps.
I would like the design to be minimalistic. With light colours: white, pink, purple.
I specialise in weight loss, flexibility, mobility.

Tessa Brogan
Personal Trainer
Email: tessa.brogan@quellmail.com
tel: 07700218493
Instagram: Mira Bloom

Target Market(s)

adults, mostly females (age 18-50).

Industry/Entity Type

Fitness

Contact Information for Business Card

Tessa Brogan
Personal Trainer
tel: 07700218493
Instagram: Mira Bloom

Font styles to use
Serif

Colors
eea4c8
fbd4d5
fdf9cf
cfeae6
cee9f5

Requirements
Nice to have
• minimalistic style
• easy to read and remember

```html
<!DOCTYPE html>
<html lang="en">
<head>
<meta charset="UTF-8">
<title>Mira Bloom Fitness Coaching – Business Card</title>
<link rel="stylesheet" href="https://fonts.googleapis.com/css2?family=Satisfy&family=Roboto:wght@400&display=swap">
<style>
  :root {
    --stage: #efeae6;
    --card: #ffffff;
    --purple: #7a2a8c;
    --grey: #4a4a4a;
    --photo-top: #8a5a44;
    --photo-bottom: #c9826d;
  }
  * { margin: 0; padding: 0; box-sizing: border-box; }
  html, body {
    width: 1200px;
    height: 766px;
    overflow: hidden;
    background: var(--stage);
  }
  .canvas {
    position: relative;
    width: 1200px;
    height: 766px;
  }
  .business-card {
    position: absolute;
    left: 75px;
    top: 83px;
    width: 1050px;
    height: 600px;
    background: var(--card);
    box-shadow: 0 6px 24px rgba(0,0,0,0.12);
    display: flex;
    flex-direction: column;
    align-items: center;
    font-family: "Roboto", Arial, sans-serif;
    color: var(--grey);
  }
  .portrait {
    margin-top: 58px;
    width: 220px;
    height: 168px;
    border-radius: 18px;
    background: linear-gradient(160deg, var(--photo-top), var(--photo-bottom));
  }
  .trainer-name {
    margin-top: 22px;
    font-family: "Satisfy", cursive;
    font-size: 66px;
    line-height: 1;
    color: var(--purple);
    font-weight: 400;
  }
  .trainer-role {
    margin-top: 6px;
    font-size: 26px;
    color: var(--grey);
  }
  .contact-band {
    margin-top: 18px;
    width: 800px;
    border-top: 2px solid var(--purple);
    border-bottom: 2px solid var(--purple);
    padding: 14px 0;
    display: flex;
    justify-content: center;
    align-items: center;
    gap: 22px;
    font-size: 25px;
  }
  .contact-item {
    display: flex;
    align-items: center;
    gap: 8px;
    color: var(--grey);
  }
  .contact-icon { width: 22px; height: 22px; fill: var(--purple); }
  .social-mark {
    width: 20px;
    height: 20px;
    background: var(--purple);
  }
  .services {
    margin-top: 16px;
    font-size: 25px;
    color: var(--grey);
  }
</style>
</head>
<body>
<main class="canvas">
  <section class="business-card">
    <div class="portrait" role="img" aria-label="Portrait photo of the trainer"></div>
    <h1 class="trainer-name">Tessa Brogan</h1>
    <p class="trainer-role">Personal Trainer</p>
    <div class="contact-band">
      <span class="contact-item">
        <svg class="contact-icon" viewBox="0 0 24 24" aria-hidden="true"><path d="M6.6 10.8a15.1 15.1 0 0 0 6.6 6.6l2.2-2.2a1 1 0 0 1 1-.25 11.4 11.4 0 0 0 3.6.57 1 1 0 0 1 1 1V20a1 1 0 0 1-1 1A17 17 0 0 1 3 4a1 1 0 0 1 1-1h3.5a1 1 0 0 1 1 1c0 1.25.2 2.45.57 3.57a1 1 0 0 1-.25 1z"/></svg>
        07700218493
      </span>
      <span class="contact-item">
        <svg class="contact-icon" viewBox="0 0 24 24" aria-hidden="true"><path d="M3 5h18a1 1 0 0 1 1 1v12a1 1 0 0 1-1 1H3a1 1 0 0 1-1-1V6a1 1 0 0 1 1-1zm1 2.2V17h16V7.2l-8 5.3z M4.8 7 12 11.7 19.2 7z"/></svg>
        tessa.brogan@quellmail.com
      </span>
      <span class="contact-item">
        <span class="social-mark" aria-hidden="true"></span>
        Mira Bloom
      </span>
    </div>
    <p class="services">PT sessions • bootcamps.</p>
  </section>
</main>
</body>
</html>
```